Doctor to Patient Management Website

I need a design for a health management website that connects doctors to patients. The website will consist of: A main page mainly describing our goal, services, and initiatives towards (Who we are AKA "About Us", Our services, Contact Us, Quick Links for health tips, Language selection, Find a doctor, search bar, Member Login Section, small glossary section below with links to all entities mentioned prior, Help section (Helpful tips and tutorials, Used to request help from admin, customer service, to resolve issues or get assistance). A profile page with two types:1) Doctor Profile: Doctor Personal info (First, Last, Middle Name, Title), Clinic, Hospital Info, Department, Credentials, Years of Experience, Patients rating, #Patients seen during the current week, #Patients seen in total, Picture, Link to email doctor, Link to print doctor's profile). Tabs for "About Me", "Contact Info", "Ratings & Comments", "Documents" (To be downloaded and uploaded by patient), "Patients (List of Patients alphabetical order by name)", "Calendar" (to see doctor's availability for booking) underneath all links. 2) Patient profile: About me, Personal Info, Height, Weight, Blood Type, Age, DOB, Name, etc..., Message and email link.Picture of patient with menu made of "Personal Data", "Biometrics", "Allergies", "Illnesses", "Medications", "Medical Procedures", "Doctors" treating the patient, "Documents" (To be downloaded and uploaded by patient). Underneath all, other patients he or she is related to (For example: family member, so patient can't connect to other patients who are family members)3) Login section: New Users will have option to register using:First Name (Required), Last Name, Middle (not required), Address (Not required), City (Required), Country (Required), Email (Not required), Phone Number (Required), Choose UserName, Password, Account Type (Doctor or Patient). Once registered, they will log in using UserName, Password, and Account_Type.Curent Users will log in using UserName, Password, and Account_Type and option to retrieve username or password.Pages to include (Login Page - Registration Page - Retrieve Username and Reset Password Page)Please see link below:https://plumcrate-adwerks.net/importance-claiming-vantorix-quibble-zarn/Pictures are attached to this project as an inspirationFYI: Dummy text can be used to fill in the business, services, and descriptive information. Feel free to include your own ideas in the layout, design, categories, patterns, and more to and showcase your talent. Design and pictures provided are available as source of ideas.

Target Market(s)

Age: 21+ / Family Oriented / Medical Sector / Metropolitan Area / Educated and non Educated Users

Industry/Entity Type

Health Care

Number of Pages Required

5+ page

Font styles to use
Sans Serif

Colors

Designer to choose colors to be used in the design.

Requirements
Must have
• Thin layer design
• Simple font - No serif
• Clean menu with light but solid colors (No Gradient effect)
Nice to have
• Different color themes (2 or 3) can be combined
• Sample pictures for illustration (either as an ad or to go with the flow of your design)
• Dashboard Feel (Suggested but not required)
Should not have
• Artistic fonts - with Serif
• Dark color themes

```html
<!DOCTYPE html>
<html lang="en">
<head>
<meta charset="utf-8">
<title>Varnell – Find a Doctor</title>
<link href="https://fonts.googleapis.com/css2?family=Montserrat:wght@400;500;600;700&display=swap" rel="stylesheet">
<style>
:root{
  --ink:#333;
  --ink-soft:#555;
  --muted:#8a8a8a;
  --line:#d6d6d6;
  --white:#fff;
  --pink:#f6c4c4;
  --blue:#d5e9fa;
  --footer:#f0f0f0;
  --hero-a:#e6eff7;
  --hero-b:#c9dcec;
}
*{box-sizing:border-box;margin:0;padding:0}
html,body{width:1200px;height:974px;overflow:hidden}
body{font-family:"Montserrat",sans-serif;color:var(--ink);background:var(--white);position:relative}
.topbar{position:absolute;top:0;left:0;width:1200px;height:33px;border-bottom:1px solid var(--line)}
.lang{position:absolute;left:172px;top:10px;font-size:12px;color:var(--ink-soft);display:flex;align-items:center;gap:6px}
.flag{width:13px;height:9px;background:#d8dbe8;border:1px solid #c45}
.tab{position:absolute;top:0;height:32px;font-size:12.5px;font-weight:600;color:var(--ink-soft);display:flex;align-items:center;justify-content:center}
.tab-login{left:776px;width:130px;background:var(--pink);clip-path:polygon(12px 0,100% 0,calc(100% - 12px) 100%,0 100%)}
.tab-find{left:895px;width:133px;background:var(--blue);clip-path:polygon(12px 0,100% 0,calc(100% - 12px) 100%,0 100%)}
.header{position:absolute;top:33px;left:0;width:1200px;height:72px}
.brand{position:absolute;left:172px;top:18px;font-size:37px;font-weight:700;color:#555;letter-spacing:.5px}
.nav{position:absolute;top:32px;left:0;font-size:14px;font-weight:600;color:var(--ink-soft)}
.nav a{position:absolute;white-space:nowrap;text-decoration:none;color:inherit}
.site-search{position:absolute;left:842px;top:25px;width:186px;height:27px;border:1px solid #e2e2e2;border-radius:14px;background:#f7f7f7;font-size:10.5px;color:#999;padding:6px 11px}
.site-search svg{position:absolute;right:9px;top:6px}
.hero{position:absolute;top:105px;left:0;width:1200px;height:420px;background:linear-gradient(180deg,var(--hero-a),var(--hero-b))}
.finder{position:absolute;top:297px;left:184px;display:flex;gap:8px}
.field{width:232px;height:45px;background:var(--white);border:1px solid #cfcfcf;font-size:12.5px;font-weight:500;color:var(--ink-soft);padding:14px 15px;position:relative}
.field .caret{position:absolute;right:11px;top:19px;width:0;height:0;border-left:5px solid transparent;border-right:5px solid transparent;border-top:6px solid #999}
.finder .btn{width:114px;height:45px;margin-left:-2px;background:var(--pink);border:1px solid #e7b0b0;font-size:12.5px;font-weight:700;color:var(--ink-soft);display:flex;align-items:center;justify-content:center;letter-spacing:.5px}
.footer{position:absolute;top:525px;left:0;width:1200px;height:449px;background:var(--footer)}
.col{position:absolute;top:62px;font-size:12.5px;color:var(--ink-soft)}
.col h3{font-size:16.5px;font-weight:500;color:var(--ink);margin-bottom:10px;display:flex;align-items:center;gap:10px}
.col p{line-height:23.2px;white-space:nowrap}
.col h3.next{margin-top:23px}
.rule{position:absolute;left:175px;top:360px;width:850px;border-top:1px solid #bbb}
.copy{position:absolute;left:172px;top:403px;font-size:12.5px;color:var(--ink)}
</style>
</head>
<body>
<div class="topbar">
  <div class="lang">Language <span class="flag"></span>
    <svg width="8" height="5" viewBox="0 0 8 5"><path d="M1 1l3 3 3-3" stroke="#666" fill="none"/></svg></div>
  <div class="tab tab-login">Member Login</div>
  <div class="tab tab-find">Find a Doctor</div>
</div>
<header class="header">
  <div class="brand">Varnell</div>
  <nav class="nav">
    <a style="left:379px">Home</a><a style="left:447px">About</a><a style="left:522px">Patients</a>
    <a style="left:610px">Reviews</a><a style="left:699px">FAQ</a><a style="left:762px">Contact</a>
  </nav>
  <div class="site-search">Search
    <svg width="12" height="12" viewBox="0 0 12 12"><circle cx="5" cy="5" r="3.8" stroke="#666" stroke-width="1.6" fill="none"/><path d="M8 8l3 3" stroke="#666" stroke-width="1.8"/></svg></div>
</header>
<section class="hero" role="img" aria-label="Photo of a team of doctors and nurses reviewing documents at a table">
</section>
<form class="finder">
  <div class="field">Doctor Name</div>
  <div class="field">Procedure Type<span class="caret"></span></div>
  <div class="field">Hospital<span class="caret"></span></div>
  <div class="btn">SEARCH</div>
</form>
<footer class="footer">
  <div class="col" style="left:173px">
    <h3><svg width="18" height="22" viewBox="0 0 18 22"><path d="M9 21s7-7.5 7-12.5A7 7 0 0 0 2 8.5C2 13.5 9 21 9 21z" fill="none" stroke="#888"/><circle cx="9" cy="8.5" r="2.5" fill="none" stroke="#888"/></svg>Contact Us</h3>
    <p>Varnell</p><p>Lorem iSum Dummt67</p><p>Easthollow &nbsp;&nbsp;&nbsp;dummy782</p><p>EH4 7QX</p>
    <h3 class="next" style="margin-top:16px"><svg width="21" height="14" viewBox="0 0 21 14"><rect x=".5" y=".5" width="20" height="13" fill="none" stroke="#888"/><path d="M.5 .5l10 7 10-7M.5 13.5l7-6M20.5 13.5l-7-6" fill="none" stroke="#888"/></svg>Email</h3>
    <p>info@varnell.com</p>
    <h3 class="next" style="margin-top:24px"><svg width="19" height="18" viewBox="0 0 19 18"><path d="M4 1l3 4-2 2c1 2.5 3.5 5 6 6l2-2 4 3-2 3C8 16 2 10 1 3z" fill="none" stroke="#888"/></svg>Phone</h3>
    <p>01632 960418</p>
  </div>
  <div class="col" style="left:392px">
    <h3>Patient Resources</h3>
    <p>Lorem ipsum dolor</p><p>Consectetur adipiscin</p><p>Do eiusmodt</p>
    <h3 class="next">General Information</h3>
    <p>Lorem ipsum dolor</p><p>Consectetur adipiscin</p><p>Do eiusmodt</p>
  </div>
  <div class="col" style="left:641px">
    <h3>Quick Links</h3>
    <p>Sed ut perspiciatis</p><p>H iste natus error sit</p><p>Gptatem accusantium dolo</p><p>Rremque laudantium,</p><p>Rotam rem aperiam, ea</p><p>Sed ut perspiciatis u</p><p>H iste natus error</p>
  </div>
  <div class="col" style="left:866px">
    <h3>Glossary</h3>
    <p>Sed ut perspiciatis und</p><p>Gptatem accusantium dolo</p><p>Rremque laudantium,</p><p>Rotam rem aperiam, ea</p><p>Sed ut perspiciatide omn</p><p>H iste natus error sit volu</p><p>Gptatem accum dolo</p><p>Rremque laudantium,</p>
  </div>
  <div class="rule"></div>
  <div class="copy">© 2019 Varnell. All rights reserved.</div>
</footer>
</body>
</html>
```